Push notification screens at app start up

We have an existing news publication app platform and are adding categories to push notifications.

We need two screens designed (each for Zorbel, Quillet and Android for a total of 6d) that show when the app is first launched.

The workflow of our app:
0. app launch screen while webservices run (no work needed)
1. information screen to the user promoting the benefits of push notification with "Next" button. (see concept attached)
2. Push categories selection screen. This will have list of category types, with on/off switch.

"Select the categories that you wish to receive occasional notices:
Breaking News (on/off switch)
Local News (on/off switch)
Sports (on/off switch)
Local Events (on/off switch)
Weather Alerts (on/off switch)
Local Deals (on/off switch)"

"Enable these categories on the next screen."
"Next" button

Background:
When I was looking around at app designs, I came across this one (http://www.plinthworks.example/design/7719034) and I really liked it. We obviously have different features on our screen, but I’d like to have this same feel. The colors used in this design are perfect.

UPDATE: I do not mean to limit your design to match the layout as the one mentioned above. Please use your creativity for the layout.

Our standard font in Helvetica Neue.

Notes:
- our app is developed for all phone devices from Zorbel 4 to Zorbel 6, so designs should be thoughtful of vertical scrolling if needed.
- our app is developed for Quillets, so we'll need designs completed as well. (We can finalize Zorbel design first, then translate the design to Quillet.)
- our app is developed for Android phones (not tablets), so we'll need designs completed as well. (We can finalize iOS design first, then translater to Android UI design guidelines).

We hope to establish a good on-going relationship with the designer for as-needed work in the future.

News

• Helvetica Neue

• Clean designs. No clutter.
• We would likely go with the standard on/off switches for both iOS and Android, but are open to small custom variations.

```html
<!DOCTYPE html>
<html lang="en">
<head>
<meta charset="utf-8">
<title>Push categories</title>
<link rel="stylesheet" href="https://fonts.googleapis.com/css2?family=Inter:wght@300;400;500&display=swap">
<style>
  :root {
    --chrome: #5c6068;
    --chrome-dark: #52565d;
    --surface: #efefef;
    --divider: #dadada;
    --text-muted: #7b7b7b;
    --icon-bg: #4e5259;
    --accent: #27b3c8;
    --switch-off: #dcdcdc;
    --white: #ffffff;
  }
  * { box-sizing: border-box; margin: 0; padding: 0; }
  html, body {
    width: 1200px;
    height: 2352px;
    overflow: hidden;
  }
  body {
    font-family: "Inter", "Helvetica Neue", Arial, sans-serif;
    font-weight: 300;
    background: var(--surface);
    position: relative;
  }
  .status-bar {
    height: 97px;
    background: var(--chrome);
    color: var(--white);
    font-size: 36px;
    font-weight: 400;
    display: flex;
    align-items: center;
    justify-content: space-between;
    padding: 0 32px;
    position: relative;
  }
  .status-left, .status-right { display: flex; align-items: center; gap: 16px; }
  .signal { display: flex; gap: 6px; }
  .signal span { width: 16px; height: 16px; border-radius: 50%; background: var(--white); }
  .signal span.empty { background: none; border: 2px solid var(--white); }
  .status-time { position: absolute; left: 50%; transform: translateX(-50%); }
  .battery {
    width: 78px; height: 34px; border: 3px solid var(--white); border-radius: 6px;
    padding: 3px; position: relative;
  }
  .battery::after {
    content: ""; position: absolute; right: -9px; top: 9px; width: 5px; height: 12px;
    background: var(--white); border-radius: 0 3px 3px 0;
  }
  .battery i { display: block; width: 100%; height: 100%; background: var(--white); border-radius: 2px; }
  .nav-bar {
    height: 151px;
    background: var(--chrome);
    border-top: 1px solid var(--chrome-dark);
    display: flex;
    align-items: center;
    justify-content: center;
    position: relative;
    color: var(--white);
  }
  .nav-back { position: absolute; left: 40px; top: 50%; transform: translateY(-50%); }
  .nav-title { font-size: 58px; font-weight: 300; }
  .intro {
    padding: 36px 60px 0;
    font-size: 46px;
    line-height: 64px;
    color: var(--text-muted);
  }
  .category-list { list-style: none; margin-top: 40px; }
  .category {
    height: 162px;
    display: flex;
    align-items: center;
    padding: 0 60px 0 50px;
    border-top: 2px solid var(--divider);
  }
  .category:last-child { border-bottom: 2px solid var(--divider); }
  .category-icon {
    width: 92px; height: 92px; border-radius: 50%;
    background: var(--icon-bg);
    display: flex; align-items: center; justify-content: center;
    flex-shrink: 0;
  }
  .category-label {
    flex: 1;
    margin-left: 48px;
    font-size: 44px;
    color: var(--text-muted);
  }
  .switch {
    width: 156px; height: 60px; border-radius: 30px;
    position: relative;
    font-size: 26px; font-weight: 500;
    display: flex; align-items: center;
  }
  .switch::after {
    content: ""; position: absolute; top: 5px; width: 50px; height: 50px;
    border-radius: 50%; background: var(--white);
    box-shadow: 0 2px 4px rgba(0,0,0,0.18);
  }
  .switch-on { background: var(--accent); color: var(--white); padding-left: 28px; }
  .switch-on::after { right: 5px; }
  .switch-off {
    background: var(--switch-off); color: #9a9a9a;
    justify-content: flex-end; padding-right: 20px;
    border: 2px solid #cfcfcf;
  }
  .switch-off::after { left: 3px; top: 3px; }
  .next-bar {
    position: absolute; left: 0; right: 0; bottom: 0;
    height: 162px;
    background: var(--chrome);
    color: var(--white);
    display: flex; align-items: center; justify-content: center;
    gap: 22px;
    font-size: 52px; font-weight: 300; letter-spacing: 1px;
  }
</style>
</head>
<body>
  <header class="status-bar">
    <div class="status-left">
      <div class="signal"><span></span><span></span><span></span><span class="empty"></span><span class="empty"></span></div>
      <span class="carrier">NORVA</span>
      <svg class="wifi" width="40" height="30" viewBox="0 0 40 30" fill="none" stroke="#fff" stroke-width="4" stroke-linecap="round">
        <path d="M4 11a23 23 0 0 1 32 0"/><path d="M10 17a14 14 0 0 1 20 0"/><circle cx="20" cy="25" r="2.5" fill="#fff" stroke="none"/>
      </svg>
    </div>
    <span class="status-time">4:21 PM</span>
    <div class="status-right">
      <span>100%</span>
      <div class="battery"><i></i></div>
    </div>
  </header>

  <nav class="nav-bar">
    <svg class="nav-back" width="30" height="50" viewBox="0 0 30 50" fill="none" stroke="#fff" stroke-width="4" stroke-linecap="round" stroke-linejoin="round">
      <path d="M24 6 6 25l18 19"/>
    </svg>
    <h1 class="nav-title">Push categories</h1>
  </nav>

  <p class="intro">Select the categories that you wish to receive occasional notices:</p>

  <ul class="category-list">
    <li class="category">
      <span class="category-icon">
        <svg width="50" height="50" viewBox="0 0 50 50" fill="#fff"><path d="M8 20h8l18-10v30L16 30H8z"/><rect x="14" y="30" width="7" height="12" rx="2"/></svg>
      </span>
      <span class="category-label">Breaking News</span>
      <span class="switch switch-on">ON</span>
    </li>
    <li class="category">
      <span class="category-icon">
        <svg width="50" height="50" viewBox="0 0 50 50" fill="none" stroke="#fff" stroke-width="3.5"><rect x="8" y="10" width="34" height="30" rx="2"/><path d="M14 18h22M14 25h10M14 32h10M29 25h7v7h-7z"/></svg>
      </span>
      <span class="category-label">Local News</span>
      <span class="switch switch-on">ON</span>
    </li>
    <li class="category">
      <span class="category-icon">
        <svg width="50" height="50" viewBox="0 0 50 50" fill="none" stroke="#fff" stroke-width="3.5"><circle cx="25" cy="25" r="16"/><path d="M9 25h32M25 9c-7 8-7 24 0 32M25 9c7 8 7 24 0 32"/></svg>
      </span>
      <span class="category-label">Sports</span>
      <span class="switch switch-on">ON</span>
    </li>
    <li class="category">
      <span class="category-icon">
        <svg width="50" height="50" viewBox="0 0 50 50" fill="none" stroke="#fff" stroke-width="3.5"><rect x="8" y="12" width="34" height="28" rx="2"/><path d="M8 20h34M16 7v9M34 7v9"/><rect x="15" y="26" width="7" height="6" fill="#fff" stroke="none"/></svg>
      </span>
      <span class="category-label">Local Events</span>
      <span class="switch switch-off">OFF</span>
    </li>
    <li class="category">
      <span class="category-icon">
        <svg width="50" height="50" viewBox="0 0 50 50" fill="none" stroke="#fff" stroke-width="3.5" stroke-linecap="round"><circle cx="20" cy="18" r="6"/><path d="M20 6v3M8 18h3M11 9l2 2M29 9l-2 2"/><path d="M16 40h20a7 7 0 0 0 0-14 9 9 0 0 0-17 2 6 6 0 0 0-3 12z" fill="#4e5259"/></svg>
      </span>
      <span class="category-label">Weather Alerts</span>
      <span class="switch switch-on">ON</span>
    </li>
    <li class="category">
      <span class="category-icon">
        <svg width="50" height="50" viewBox="0 0 50 50" fill="none" stroke="#fff" stroke-width="3.5" stroke-linejoin="round"><path d="M8 10h16l18 18-14 14L10 24z"/><circle cx="17" cy="17" r="3" fill="#fff" stroke="none"/></svg>
      </span>
      <span class="category-label">Local Deals</span>
      <span class="switch switch-off">OFF</span>
    </li>
  </ul>

  <footer class="next-bar">
    <span>NEXT</span>
    <svg width="22" height="40" viewBox="0 0 22 40" fill="none" stroke="#fff" stroke-width="3.5" stroke-linecap="round" stroke-linejoin="round"><path d="M4 4l14 16L4 36"/></svg>
  </footer>
</body>
</html>
```